Commercial Real Estate Corporate Site

Our company sells an ERP software to Commercial Real Estate Companies, this project is part of a marketing and sales relaunch of the company.

See attached for PDF formatted Design brief

The software is a modular system where client’s can adopt one module at a time. Our customers are corporate clients who own between 10M and 10B of real estate properties. The typical customer is from the IT or the Financial arm of the company. Our differentiation in the market is that our system is built on a no-code environment, so making changes for the client is quick. Incumbents in the market have long implementation cycles, and customization is often not possible. Competitors are Quorvel, TKB, PlotNest, Vumora.

We need a design for our site which will be implemented into Brevo Forge. **All designs must be compatible with the newest version of Brevo Forge.**

We have produced the following attached assets to use in the website design.:

1. Logo
2. Brand Guidelines
3. Content for Pages
4. Menu Structures
5. Illustrations (modules)
I can't attach them because the files are too big, so they're in this google drive instead:
https://files.examplestore.net/share/k29Xa7Lq0Pz3Rt8MwB5nYc4Hv1Jd6Fe?mode=view

The mechanic for our sales process is as follows:

1. We find on module from our application that a client is interested in. The illustrations that we’ve attached represent the individual modules (elements) of the software.
1. For instance, one of our current customers has purchased a commissions module from us which helps calculate the commission that brokers receive for buying and selling their properties.
2. We provide immense value through the module, and then keep in sales communication with the client to determine which other modules we can implement for them.
1. For instance, in the example above, the client is so happy with the commissions module that they want to start working with our leasing module as well. In the next business quarter, they also choose to add our financials module to their business systems.

### Logo

Attached

### Brand Guidelines

Attached

We are open to suggestions on the secondary colour palette.

### **Site Copy**

**We require the following pages to be created; For now, we will do one Market Page, one Product Page, and one Platform / Services Page, and we will use those as inspiration to create the other dozen Marketing Pages and 30 or so Product Pages.**

**Homepage**

Attached

**Market Page** - look at the quorvel site under the Office, Industrial, Retail (https://www.quorvel.com/products/quorvel-commercial-suite/)

**Product** - One product provided, but there will be 30 - look at the vumora page

(https://www.vumora.com/products/general-accounting)

**Platform / Services Page** - pages that tell the story of our platform and services, content to be provided - the platform will use our modules as it highlights the story of the configurability and composability of the platform. Instead of the icons that they use, we want to use our modules.

- https://www.pelbrix.com/enterprise-applications-platform
- https://www.pelbrix.com/cloud-architecture

**Team Page** - just add sample content for starters (6 Team Members to start)

**Schedule Demo Page** - the call to action for all pages

(https://go.vumora.com/schedule-demo.html)

### Menu Structure

The menu is provided as an attachment.

### Illustrations Information

A note about the illustrations - we have provided an illustrator file with the modules, and if you’d like you can arrange the in any way that you’d like to. We especially like when the modules are positioned like a periodic table of the elements.

Our existing clients are

- Torvane Coop - https://www.torvanecoop.com/real-estate/
- Dalsworth Realestate https://dalsworth.com

Our competitors are

- Quorvel - www.quorvel.com
- TKB - [www.tkbsoftware.com](https://www.tkbsoftware.com/) (we don’t like how this one looks)
- Vumora - www.vumora.com
- Plotnest - www.plotnest.com

Design inspiration

- https://lark-studio.brevosite.com/velmo
- Corporate
- Established
- Modern

### Stock Images Guidance

- https://www.drafta.net/design/QXR7Lm2TpWz/Hk9vN3c8Yd41-FbqsaZRr/edit?utm_content=QXR7Lm2TpWz&utm_campaign=designshare&utm_medium=link2&utm_source=sharebutton

Target Market(s)

Commercial Real Estate Companies - they typically own a portfolio of 50 - 5000 real estate properties and need a software to manage it all.

Coding

Coded - Design and coding required

Number of Pages Required

5+ page

Font styles to use
Other font styles liked:
• Fonts defined in brand guideline

Requirements
Must have
• Brevo Forge, Use the Elemental Design, Download ai.zip and png.zip Use Brand Guideline,
Nice to have
• Check design breif

```html
<!DOCTYPE html>
<html lang="en">
<head>
<meta charset="utf-8">
<title>Halveo — Enterprise Applications Platform for Real Estate</title>
<link rel="stylesheet" href="https://fonts.googleapis.com/css2?family=Montserrat:wght@400;500;600;700;800;900&family=Orbitron:wght@500;600&display=swap">
<style>
:root{
  --red:#c00000;
  --red-dark:#a80000;
  --red-bright:#e0201b;
  --ink:#1e1e1e;
  --text:#555;
  --muted:#777;
  --light:#f4f4f4;
  --white:#fff;
  --line:#d4d4d4;
  --placeholder-a:#e6e8ea;
  --placeholder-b:#cfd3d6;
}
*{box-sizing:border-box;margin:0;padding:0}
html,body{width:1200px;height:3523px;overflow:hidden}
body{font-family:"Montserrat",sans-serif;color:var(--ink);background:var(--white);position:relative}
.abs{position:absolute}
.center{text-align:center}
.tech{font-family:"Orbitron",sans-serif;font-weight:500;letter-spacing:.5px;text-transform:uppercase}
.btn{position:absolute;display:flex;align-items:center;justify-content:center;background:var(--red);color:#fff;font-weight:700;font-size:17px;text-decoration:none}

/* hero */
.hero{left:0;top:0;width:1200px;height:700px;background:linear-gradient(180deg,#2d2f33 0%,#4a5a6e 35%,#7a8ea6 60%,#3b4654 100%)}
.hero-photo{left:0;top:0;width:1200px;height:700px;background:radial-gradient(ellipse at 50% 35%,rgba(150,175,205,.55),rgba(20,22,26,.6) 75%)}
.brand{left:68px;top:46px;font-weight:800;font-size:30px;color:var(--red-bright);display:flex;align-items:center;gap:8px}
.brand .dot{width:14px;height:14px;border-radius:50%;background:var(--red-bright)}
.nav{left:216px;top:54px;display:flex;gap:18px;font-size:15px;color:#d8dce2}
.nav span.active{color:#fff;font-weight:700}
.nav .chev{display:inline-block;width:6px;height:6px;border-right:1.5px solid currentColor;border-bottom:1.5px solid currentColor;transform:rotate(45deg);margin:0 0 3px 5px}
.hero-kicker{left:0;width:1200px;top:205px;color:#fff;font-size:18px}
.hero-title{left:0;width:1200px;top:250px;color:#fff;font-weight:800;font-size:34px;line-height:41px;text-transform:uppercase}
.hero-copy{left:227px;width:746px;top:357px;color:#e8ebef;font-size:15px;line-height:28.5px}
.hero-contact{left:0;width:1200px;top:536px;color:#fff;font-size:17px}

/* intro band */
.kicker{font-size:17px;color:var(--ink)}
.kicker em{font-style:normal;color:var(--red-bright)}
.band-title{left:0;width:1200px;top:723px;font-weight:800;font-size:32px;color:var(--ink)}

/* about */
.frame{left:148px;top:865px;width:413px;height:476px;border:3px solid var(--red);border-radius:16px}
.photo{left:66px;top:888px;width:477px;height:432px;border-radius:14px;background:linear-gradient(120deg,#b9c6cf 0%,#d9cdbf 40%,#8a6e5a 70%,#e8e6e2 100%)}
.feature{left:616px;width:517px}
.feat-icon{width:80px;height:80px;border-radius:50%;background:#fff;box-shadow:0 6px 18px rgba(0,0,0,.12);display:flex;align-items:center;justify-content:center}
.feat-icon.solid{background:radial-gradient(circle at 40% 35%,#b01010,#5a0000);box-shadow:0 6px 14px rgba(120,0,0,.3)}
.feat-title{font-weight:600;font-size:18.5px;line-height:25px;color:var(--ink)}
.feat-title.red{color:var(--red);font-weight:700}
.feat-text{font-size:12.5px;line-height:18.6px;color:var(--muted)}
.see{font-size:15px;color:var(--muted)}
.see.red{color:var(--red-bright)}
.divider{left:616px;width:517px;height:1px;background:var(--line)}

/* modules */
.grey-band{left:0;top:1409px;width:1200px;height:500px;background:var(--light)}
.section-title{font-weight:900;font-size:34px;color:#2a2a2a;text-shadow:0 2px 3px rgba(0,0,0,.18)}
.cube{background:linear-gradient(135deg,#f2f2f2,#9a9a9a);box-shadow:-14px 10px 14px rgba(0,0,0,.15)}
.cube.dark{background:linear-gradient(135deg,#8a8a8a,#3c3c3c)}
.pillar{width:320px}
.pillar h3{font-weight:600;font-size:20px;color:var(--ink);margin:14px 0 12px}
.pillar p{font-size:13px;line-height:18.6px;color:var(--muted)}

/* platform */
.modules-art{left:435px;top:2148px;width:322px;height:256px;border-radius:10px;background:linear-gradient(160deg,var(--placeholder-a),var(--placeholder-b))}
.plat h3{font-weight:600;font-size:20px;line-height:25px;color:var(--ink)}
.plat p{font-size:13px;line-height:18.6px;color:var(--muted);margin-top:10px}

/* discover */
.disc-band{left:0;top:2691px;width:1200px;height:440px;background:var(--light)}
.disc-copy{left:300px;width:600px;top:2925px;font-size:15px;line-height:20px;color:var(--text)}

/* footer */
.footer{left:0;top:3110px;width:1200px;height:413px;background:var(--red-dark);clip-path:polygon(0 25px,1200px 0,1200px 413px,0 413px)}
.f-brand{left:86px;top:3228px;font-weight:700;font-size:30px;color:#fff}
.f-contact{left:226px;color:#fff;font-size:13px;line-height:21px}
.f-contact b{font-weight:600}
.f-col{color:#fff;font-size:13px}
.f-col h4{font-weight:700;font-size:13px;margin-bottom:21px}
.f-col li{list-style:none;height:40px;font-weight:500}
.f-top{left:1071px;top:3225px;width:42px;height:42px;border:1.5px solid #fff;border-radius:50%}
.copyright{left:0;width:1200px;top:3479px;font-size:8px;color:#f0d0d0}
</style>
</head>
<body>

<!-- Hero -->
<div class="abs hero" role="img" aria-label="Upward view of city skyscrapers against the sky"></div>
<div class="abs hero-photo"></div>

<div class="abs brand"><span class="dot"></span>Halveo</div>
<nav class="abs nav">
  <span class="active">Home</span>
  <span>Markets<i class="chev"></i></span>
  <span>Products<i class="chev"></i></span>
  <span>Platform<i class="chev"></i></span>
  <span>Services<i class="chev"></i></span>
  <span>Resources<i class="chev"></i></span>
  <span>About Us<i class="chev"></i></span>
  <span>Contact Us<i class="chev"></i></span>
</nav>
<a class="btn" style="left:1000px;top:48px;width:133px;height:34px;font-size:15px">Start Demo</a>

<div class="abs hero-kicker center tech">Welcome to Halveo</div>
<h1 class="abs hero-title center">An infinitely composable enterprise<br>applications platform (EAP) for real estate</h1>
<p class="abs hero-copy center">Far beyond what’s possible with tired, legacy real estate ERP software, Halveo offers a complete industry solution, architected as flexible modules that can be assembled and configured into an infinite combination of processes and workflows.</p>
<a class="btn" style="left:512px;top:476px;width:175px;height:47px">Start Demo</a>
<div class="abs hero-contact center">Contact Us</div>

<!-- Intro band -->
<svg class="abs" style="left:0;top:690px" width="1200" height="115" viewBox="0 690 1200 115">
  <polygon points="0,690 1200,690 1200,702 876,732 814,796 386,796 326,732 0,707" fill="#f6f6f6"/>
  <polyline points="0,707 326,732 386,796 814,796 876,732 1200,702" fill="none" stroke="#c00000" stroke-width="3"/>
</svg>
<div class="abs kicker tech center" style="left:0;width:1200px;top:697px">One Solution - <em>Infinite Possibilities</em></div>
<h2 class="abs band-title center">HALVEO ENTERPRISE</h2>

<!-- About -->
<div class="abs frame"></div>
<div class="abs photo" role="img" aria-label="Two business colleagues high-fiving at a desk with a laptop"></div>

<div class="abs feature" style="top:846px;display:flex;gap:17px">
  <div class="feat-icon solid" style="flex:none"></div>
  <div style="width:420px">
    <div class="feat-title red">Halveo</div>
    <p class="feat-text" style="margin-top:6px">Halveo was born from decades of real estate enterprise software development and implementation experience - Spanning hundreds of blue chip global real estate investment firms. But Halveo is unlike anything you’ve experienced before.</p>
    <div class="see red" style="margin-top:8px">See More</div>
  </div>
</div>
<div class="abs divider" style="top:1019px"></div>

<div class="abs feature" style="top:1041px;display:flex;gap:23px">
  <div class="feat-icon" style="flex:none">
    <svg width="38" height="24" viewBox="0 0 38 24" fill="none" stroke="#c00000" stroke-width="3" stroke-linecap="round" stroke-linejoin="round"><polyline points="2,22 13,11 21,17 35,4"/><polyline points="25,4 35,4 35,13"/></svg>
  </div>
  <div style="width:414px;padding-top:10px">
    <div class="feat-title">No more multi-million-dollar disruptive implementations.</div>
    <p class="feat-text" style="margin-top:12px">No more waiting for upgrades and enhancements that never come. No more trailing projects and disappointing customizations. No more settling for less than exactly what you want.</p>
    <div class="see" style="margin-top:8px">See More</div>
  </div>
</div>
<div class="abs divider" style="top:1220px"></div>

<div class="abs feature" style="top:1242px;display:flex;gap:27px">
  <div class="feat-icon" style="flex:none">
    <svg width="34" height="34" viewBox="0 0 34 34" fill="none" stroke="#c00000" stroke-width="2" stroke-linejoin="round"><path d="M13 6 L15.5 14.5 L24 17 L15.5 19.5 L13 28 L10.5 19.5 L2 17 L10.5 14.5 Z"/><path d="M26 2 L27.3 5.7 L31 7 L27.3 8.3 L26 12 L24.7 8.3 L21 7 L24.7 5.7 Z"/><path d="M26 22 L27 25 L30 26 L27 27 L26 30 L25 27 L22 26 L25 25 Z"/></svg>
  </div>
  <div style="width:410px">
    <div class="feat-title">You can begin using Halveo simply</div>
    <p class="feat-text" style="margin-top:10px">Starting with a single module. Then, you can build-on with additional modules at your own pace.</p>
  </div>
</div>
<a class="btn" style="left:717px;top:1323px;width:128px;height:37px">Start Now</a>

<!-- Modules -->
<div class="abs grey-band"></div>
<svg class="abs" style="left:0;top:1405px" width="1200" height="520" viewBox="0 1405 1200 520">
  <polygon points="0,1409 600,1471 1200,1409 1200,1416 600,1478 0,1416" fill="#c00000"/>
  <polygon points="0,1909 0,1840 600,1900 1200,1840 1200,1909" fill="#fff"/>
  <polygon points="0,1837 600,1898 1200,1837 1200,1845 600,1912 0,1845" fill="#c00000"/>
</svg>
<div class="abs kicker tech center" style="left:0;width:1200px;top:1510px">Simple - <em>Secure</em> - Scalable</div>
<h2 class="abs section-title center" style="left:0;width:1200px;top:1532px">The Modules of Halveo</h2>
<div class="abs cube" style="left:338px;top:1525px;width:34px;height:34px" role="img" aria-label="Light grey cube decoration"></div>
<div class="abs cube dark" style="left:832px;top:1521px;width:34px;height:34px" role="img" aria-label="Dark grey cube decoration"></div>

<div class="abs pillar center" style="left:52px;top:1618px">
  <svg width="70" height="62" viewBox="0 0 70 62" fill="none" stroke="#c00000" stroke-width="3" stroke-linejoin="round"><rect x="3" y="26" width="13" height="32" rx="2"/><path d="M16 30 L28 10 Q30 2 36 4 Q40 6 38 16 L36 24 L62 24 Q68 26 66 32 L60 54 Q58 58 52 58 L16 58"/></svg>
  <h3>Simple</h3>
  <p>Halveo provides a user-friendly and intuitive interface, simplifying complex processes and workflows for effortless navigation and understanding.</p>
</div>
<div class="abs pillar center" style="left:432px;top:1618px">
  <svg width="50" height="62" viewBox="0 0 50 62" fill="none" stroke="#c00000" stroke-width="3"><path d="M12 26 V16 Q12 3 25 3 Q38 3 38 16 V26"/><rect x="4" y="26" width="42" height="33" rx="7"/><line x1="25" y1="38" x2="25" y2="47" stroke-linecap="round"/></svg>
  <h3>Secure</h3>
  <p>With robust encryption protocols and advanced cybersecurity measures, Halveo ensures the utmost protection of sensitive data, safeguarding against cyber threats and unauthorized access.</p>
</div>
<div class="abs pillar center" style="left:814px;top:1618px">
  <svg width="64" height="62" viewBox="0 0 64 62" fill="none" stroke="#c00000" stroke-width="3"><circle cx="32" cy="31" r="23"/><path d="M58 6 Q66 14 40 38 Q14 60 6 54 Q0 48 16 30"/></svg>
  <h3>Scalable</h3>
  <p>Designed to seamlessly adapt to your growing business needs, Halveo offers scalability without limitations, accommodating expansion and evolution while maintaining optimal performance.</p>
</div>

<!-- Platform -->
<div class="abs tech center" style="left:0;width:1200px;top:1970px;font-size:17px">Platform</div>
<h2 class="abs section-title center" style="left:0;width:1200px;top:1990px;line-height:41px">Stop settling for less than<br>exactly what you want</h2>

<svg class="abs" style="left:0;top:2190px" width="1200" height="350" viewBox="0 2190 1200 350" fill="none" stroke="#c00000" stroke-width="1.5">
  <polyline points="435,2212 256,2212 256,2284"/>
  <polyline points="757,2208 980,2208 980,2280"/>
  <line x1="599" y1="2404" x2="599" y2="2530"/>
  <circle cx="256" cy="2285" r="3" fill="#c00000"/>
  <circle cx="980" cy="2281" r="3" fill="#c00000"/>
  <circle cx="599" cy="2531" r="3" fill="#c00000"/>
</svg>
<div class="abs modules-art" role="img" aria-label="Illustration of software module blocks arranged like a periodic table"></div>

<div class="abs plat center" style="left:108px;width:296px;top:2297px">
  <h3>Simplicity and Scalability</h3>
  <p>Simplicity and Scalability: Halveo combines the simplicity of custom, no-code software, enabling users to adapt to changing business needs without limitations.</p>
</div>
<div class="abs plat center" style="left:826px;width:296px;top:2293px">
  <h3>Modular Approach and Innovation</h3>
  <p>Halveo’ modular approach allows for rapid innovation and business transformation by enabling users to customize workflows to their needs, replacing traditional ERP technology with a modern, flexible solution.</p>
</div>
<div class="abs plat center" style="left:449px;width:302px;top:2549px">
  <h3>Security and Compliance</h3>
  <p>Halveo provides security and confidence through a complete, SOC 2 compliant industry solution, ensuring protection of sensitive data from cyber threats and unauthorized access.</p>
</div>

<!-- Discover -->
<div class="abs disc-band"></div>
<svg class="abs" style="left:0;top:2688px" width="1200" height="70" viewBox="0 2688 1200 70">
  <polygon points="0,2688 600,2747 1200,2688 1200,2695 600,2754 0,2695" fill="#c00000"/>
</svg>
<h2 class="abs section-title center" style="left:0;width:1200px;top:2818px;line-height:41px">Discover Halveo: Your Modern<br>Alternative to Legacy ERP Systems!</h2>
<p class="abs disc-copy center">Discover Halveo: Your Modern Alternative to Legacy ERP Systems! With decades of expertise in real estate software development and implementation across numerous global firms, including blue-chip real estate investment companies, we deliver unparalleled enterprise excellence. Take the leap into the future with Halveo!</p>
<a class="btn" style="left:506px;top:3037px;width:186px;height:49px">Explore Now</a>

<div class="abs cube" style="left:64px;top:2845px;width:54px;height:54px" role="img" aria-label="Grey cube decoration"></div>
<div class="abs cube" style="left:185px;top:2893px;width:54px;height:54px" role="img" aria-label="White cube decoration"></div>
<div class="abs cube dark" style="left:111px;top:2941px;width:54px;height:54px" role="img" aria-label="Dark grey cube decoration"></div>
<div class="abs cube" style="left:1082px;top:2845px;width:54px;height:54px" role="img" aria-label="Grey cube decoration"></div>
<div class="abs cube" style="left:963px;top:2893px;width:54px;height:54px" role="img" aria-label="White cube decoration"></div>
<div class="abs cube dark" style="left:1034px;top:2941px;width:54px;height:54px" role="img" aria-label="Dark grey cube decoration"></div>

<!-- Footer -->
<footer class="abs footer"></footer>
<div class="abs f-brand">Halveo</div>
<div class="abs f-contact" style="top:3228px;display:flex;gap:8px">
  <svg width="14" height="14" viewBox="0 0 14 14" fill="none" stroke="#fff" stroke-width="1.4" style="margin-top:3px"><circle cx="7" cy="7" r="5.5"/><circle cx="7" cy="7" r="2"/></svg>
  <div style="line-height:18px"><b>Lorem ipsum dolor sit amet</b><br><span style="font-size:11px">consectetur adipiscing elit</span><br><span style="font-size:11px">Fusce lobortis rhoncus ipsum</span></div>
</div>
<div class="abs f-contact" style="top:3302px;display:flex;gap:8px">
  <svg width="14" height="14" viewBox="0 0 14 14" fill="none" stroke="#fff" stroke-width="1.4" style="margin-top:3px"><path d="M2 2 L5 1.5 L6.5 5 L4.8 6.3 Q6 9 8 9.2 L9 7.5 L12.5 9 L12 12 Q5 13 2 2 Z"/></svg>
  <div><b>Phone:</b> (123) 456-7890</div>
</div>
<div class="abs f-contact" style="top:3334px;display:flex;gap:8px">
  <svg width="14" height="14" viewBox="0 0 14 14" fill="none" stroke="#fff" stroke-width="1.4" style="margin-top:3px"><path d="M2 2 H12 V9 H6 L3 12 V9 H2 Z"/></svg>
  <div><b>Email:</b> email@email.com</div>
</div>

<div class="abs f-col" style="left:473px;top:3230px"><h4>About Us</h4><ul><li>Company</li><li>Customers</li><li>Partners</li></ul></div>
<div class="abs f-col" style="left:568px;top:3230px"><h4>Markets</h4><ul><li>Multifam</li><li>Office</li><li>Industrial</li><li>Retail</li></ul></div>
<div class="abs f-col" style="left:653px;top:3230px"><h4>Products</h4><ul><li>Resident Pay</li><li>Resident Portal</li><li>Marketing</li><li>Accounting</li><li>Utilities</li></ul></div>
<div class="abs f-col" style="left:776px;top:3230px"><h4>Platform</h4><ul><li>Composable</li><li>Modularity</li><li>Elemental</li><li>Customizable</li><li>Workflows</li></ul></div>
<div class="abs f-col" style="left:890px;top:3230px"><h4>Services</h4><ul><li>Managed</li><li>Data</li></ul></div>
<div class="abs f-col" style="left:977px;top:3230px"><h4>Resources</h4><ul><li>News</li><li>Blog</li><li>Stories</li><li>Ebook</li><li>Training</li></ul></div>

<div class="abs f-top">
  <svg width="42" height="42" viewBox="0 0 42 42" fill="none" stroke="#fff" stroke-width="1.6" stroke-linecap="round" style="position:absolute;left:-1.5px;top:-1.5px"><line x1="21" y1="30" x2="21" y2="12"/><polyline points="14,19 21,12 28,19"/></svg>
</div>
<div class="abs copyright center">Copyright@halveo 2024. All Rights Reserved</div>

</body>
</html>
```